Northfield Builders Guild Business card

We are looking for a new business card design with photo included.
Our business is a nonprofit construction contractor membership organization. We offer business education, assist with business setup and licensing, provide safety training, and provide a member directory.
URL: www.builderslinkguild.org
Color code:
CMYK: 0 cyan, 42 magenta, 100 yellow, 0 black for Print.
Hexidecimal: #FF9900
RGB: R 255; G 153; B 0

```html
<!DOCTYPE html>
<html lang="en">
<head>
<meta charset="utf-8">
<title>Northfield Builders Guild – Business Card</title>
<link href="https://fonts.googleapis.com/css2?family=Montserrat:wght@500;600;700;800&display=swap" rel="stylesheet">
<style>
  :root {
    --orange: #ff9900;
    --charcoal: #333233;
    --white: #ffffff;
    --backdrop: #1c1c1c;
  }
  * { margin: 0; padding: 0; box-sizing: border-box; }
  html, body { width: 1200px; height: 1015px; overflow: hidden; }
  body {
    background: var(--backdrop);
    font-family: "Montserrat", Arial, sans-serif;
    display: flex;
    flex-direction: column;
    align-items: center;
    justify-content: center;
    gap: 55px;
  }
  .card {
    position: relative;
    width: 700px;
    height: 400px;
    overflow: hidden;
    box-shadow: 0 12px 30px rgba(0,0,0,.55);
  }
  .card-art { position: absolute; inset: 0; width: 100%; height: 100%; z-index: 0; }
  .card > :not(.card-art) { z-index: 1; }

  .brand-name {
    position: absolute;
    color: var(--charcoal);
    font-weight: 800;
    line-height: 1.05;
    text-transform: uppercase;
    white-space: nowrap;
  }

  /* back side */
  .card-back { background: var(--charcoal); }
  .website {
    position: absolute; right: 40px; top: 28px;
    color: var(--white); font-size: 16px; font-weight: 500;
  }
  .website .domain { color: var(--orange); }
  .services {
    position: absolute; left: 46px; top: 90px;
    list-style: none; color: var(--white);
    font-size: 15px; font-weight: 500; letter-spacing: .3px; line-height: 1.25;
  }
  .services li { position: relative; padding-left: 22px; margin-bottom: 14px; white-space: nowrap; }
  .services li::before {
    content: ""; position: absolute; left: 0; top: 6px;
    width: 8px; height: 8px; border-radius: 50%; background: var(--orange);
  }
  .card-back .brand-name { right: 40px; top: 250px; font-size: 26px; text-align: right; }

  /* front side */
  .card-front { background: var(--white); }
  .card-front .brand-name { left: 50px; top: 130px; font-size: 36px; }
  .contact {
    position: absolute; right: 30px; top: 150px;
    text-align: right; color: var(--white);
    font-size: 14px; font-weight: 500; line-height: 1.5;
    white-space: nowrap;
  }
  .contact .person { color: var(--orange); font-size: 22px; font-weight: 800; line-height: 1.1; }
  .contact .role { font-size: 12px; font-weight: 600; letter-spacing: .5px; margin-bottom: 8px; }
  .contact .line { display: flex; justify-content: flex-end; align-items: center; gap: 8px; }
  .contact .tag { color: var(--orange); }
  .icon {
    width: 18px; height: 18px; border-radius: 50%;
    background: var(--orange); display: inline-flex; align-items: center; justify-content: center;
  }
  .icon svg { width: 11px; height: 11px; }
  .address { margin-top: 12px; font-size: 14px; }
</style>
</head>
<body>

<section class="card card-back" aria-label="Business card back">
  <svg class="card-art" viewBox="0 0 700 400" aria-hidden="true">
    <defs>
      <path id="back-wave" d="M760 88 L700 88 C560 88 470 120 420 190 C360 280 320 370 160 400 L160 460 L760 460 Z"/>
    </defs>
    <use href="#back-wave" fill="var(--orange)"/>
    <use href="#back-wave" fill="var(--white)" transform="translate(8 6)"/>
    <use href="#back-wave" fill="var(--orange)" transform="translate(14 10)"/>
    <use href="#back-wave" fill="var(--white)" transform="translate(20 14)"/>
  </svg>
  <p class="website">www.<span class="domain">builderslinkguild</span>.org</p>
  <ul class="services">
    <li>BUSINESS EDUCATION</li>
    <li>ASSIST WITH BUSINESS SETUP<br>AND LICENSING</li>
    <li>PROVIDE SAFETY TRAINING</li>
    <li>PROVIDE A MEMBER DIRECTORY</li>
  </ul>
  <p class="brand-name">Northfield<br>Builders Guild</p>
</section>

<section class="card card-front" aria-label="Business card front">
  <svg class="card-art" viewBox="0 0 700 400" aria-hidden="true">
    <defs>
      <path id="front-wave" d="M760 40 L700 40 C540 40 480 70 440 150 C390 260 360 330 200 335 L-40 335 L-40 460 L760 460 Z"/>
    </defs>
    <use href="#front-wave" fill="var(--orange)" transform="translate(-18 -12)"/>
    <use href="#front-wave" fill="var(--white)" transform="translate(-12 -8)"/>
    <use href="#front-wave" fill="var(--orange)" transform="translate(-6 -4)"/>
    <use href="#front-wave" fill="var(--charcoal)"/>
  </svg>
  <p class="brand-name">Northfield<br>Builders Guild</p>
  <div class="contact">
    <p class="person">DANIEL MERCER</p>
    <p class="role">MANAGING DIRECTOR</p>
    <p class="line">(541) 302-7781 <span class="tag">(Office)</span>
      <span class="icon"><svg viewBox="0 0 24 24"><path d="M6.6 10.8a15 15 0 0 0 6.6 6.6l2.2-2.2a1 1 0 0 1 1-.25 11 11 0 0 0 3.6.6 1 1 0 0 1 1 1V20a1 1 0 0 1-1 1A17 17 0 0 1 3 4a1 1 0 0 1 1-1h3.5a1 1 0 0 1 1 1 11 11 0 0 0 .6 3.6 1 1 0 0 1-.25 1z" fill="var(--charcoal)"/></svg></span></p>
    <p class="line">800-555-0147
      <span class="icon"><svg viewBox="0 0 24 24"><rect x="6" y="2" width="12" height="20" rx="2" fill="var(--charcoal)"/><rect x="8" y="5" width="8" height="12" fill="var(--orange)"/></svg></span></p>
    <p class="line">541.302.7790
      <span class="icon"><svg viewBox="0 0 24 24"><rect x="6" y="3" width="12" height="6" fill="var(--charcoal)"/><rect x="3" y="9" width="18" height="8" rx="1" fill="var(--charcoal)"/><rect x="7" y="14" width="10" height="7" fill="var(--charcoal)"/></svg></span></p>
    <p class="line">hello@nbguild.org
      <span class="icon"><svg viewBox="0 0 24 24"><rect x="2" y="5" width="20" height="14" rx="1" fill="var(--charcoal)"/><path d="M2 6l10 7 10-7" stroke="var(--orange)" stroke-width="2" fill="none"/></svg></span></p>
    <p class="address">2400 Ridgeway Ave<br>Suite #210, Northfield, OR 97400</p>
  </div>
</section>

</body>
</html>
```